Business cards in digital learning for freelancer

Hello, I need a business cards in french. I work in the Digital learning industries as freeelancer; I'm an expert in digital learning. I work in France. My customer are in the health industry, pharmaceutical industry, and training organization. I've got a logo. I offer three services: consulting, Design, and Training. In the consulting, I offers coaching to choose your digital learning tools and the digital learning strategy. For the Design, I product differents level of elearning like rapid-learning, elearning, micro-learning, video-learning. And for the training service, I've create training about pedagogy, digital learning management project, Digital learning design.
I join my Logo create in this platform. My universe is gamified. I like the life, and I'm very social. I want a card like I'm I. I love Art (painting), Europeen comics. I use in my visual support "permanent maker" font and caracters. I would like cards: elegant, modern, Top class. If you need any information, you can ask me.
thanks for ideas

Target Market(s)

in health industries and training organization for Training manager, instructor, human resources director

Contact Information for Business Card

Phone number : 06 71 38 95 14 , mail: bastiengolmier@quelmoto.fr, web: bastiengolmier.fr , Carrivo

Font styles to use
Sans Serif

Requirements
Must have
• Use my logo and write my 3 services (consulting, training, design)

```html
<!DOCTYPE html>
<html lang="fr">
<head>
<meta charset="utf-8">
<title>Golmier – cartes de visite</title>
<link rel="stylesheet" href="https://fonts.googleapis.com/css2?family=Arimo:wght@400;700&family=Cinzel:wght@500&display=swap">
<style>
  :root {
    --stage: #000000;
    --card: #333335;
    --orange: #f07424;
    --text-light: #d6d6d6;
    --rule: #5a5a5c;
  }
  html, body {
    margin: 0;
    width: 1200px;
    height: 900px;
    overflow: hidden;
    background: var(--stage);
  }
  .canvas {
    position: relative;
    width: 1200px;
    height: 900px;
    font-family: "Arimo", Arial, sans-serif;
  }
  .card {
    position: absolute;
    width: 458px;
    height: 283px;
    background: var(--card);
    border-radius: 15px;
  }
  .card--front { left: 138px; top: 265px; }
  .card--back { left: 625px; top: 268px; }

  /* front */
  .brand-block {
    position: absolute;
    left: 20px;
    width: 196px;
    top: 150px;
    text-align: center;
  }
  .brand-name {
    font-weight: 700;
    font-size: 28px;
    letter-spacing: 1px;
    color: var(--orange);
  }
  .divider {
    position: absolute;
    left: 229px;
    top: 65px;
    width: 1px;
    height: 150px;
    background: var(--rule);
  }
  .contact {
    position: absolute;
    left: 253px;
    top: 88px;
    color: var(--text-light);
  }
  .contact__name {
    font-family: "Cinzel", "Times New Roman", serif;
    font-weight: 500;
    font-size: 19px;
    color: var(--orange);
    margin: 0;
    line-height: 1.1;
  }
  .contact__role {
    font-size: 14px;
    margin: 2px 0 18px;
  }
  .contact__list {
    list-style: none;
    margin: 0;
    padding: 0;
    font-size: 13.5px;
    line-height: 16.5px;
  }
  .contact__list li {
    display: flex;
    align-items: center;
    gap: 5px;
  }
  .contact__icon {
    width: 11px;
    height: 11px;
    flex: none;
  }

  /* back */
  .back-brand {
    position: absolute;
    left: 0;
    right: 0;
    top: 96px;
    text-align: center;
  }
  .back-brand .brand-name { font-size: 40px; }
  .services {
    position: absolute;
    left: 0;
    right: 0;
    top: 180px;
    text-align: center;
    font-size: 12.5px;
    color: var(--text-light);
    letter-spacing: 0.2px;
  }
  .services__dot {
    display: inline-block;
    width: 7px;
    height: 7px;
    border-radius: 50%;
    background: var(--orange);
    margin: 0 5px;
    vertical-align: 1px;
  }
  .social {
    position: absolute;
    left: 124px;
    width: 211px;
    top: 206px;
    display: flex;
    align-items: center;
    gap: 8px;
    font-size: 12px;
    color: var(--text-light);
  }
  .social__rule { flex: 1; height: 1px; background: var(--rule); }
  .social__dot { width: 9px; height: 9px; border-radius: 50%; background: var(--orange); }
</style>
</head>
<body>
<main class="canvas">
  <section class="card card--front" aria-label="Recto">
    <div class="brand-block">
      <div class="brand-name">GOLMIER</div>
    </div>
    <div class="divider"></div>
    <div class="contact">
      <h1 class="contact__name">Bastien Golmier</h1>
      <p class="contact__role">Managing Director</p>
      <ul class="contact__list">
        <li>
          <svg class="contact__icon" viewBox="0 0 12 12" aria-hidden="true"><path d="M2.5 1 L4.5 1 L5.2 3.5 L4 4.5 C4.7 6 6 7.3 7.5 8 L8.5 6.8 L11 7.5 L11 9.5 C11 10.3 10.3 11 9.5 11 C5 10.7 1.3 7 1 2.5 C1 1.7 1.7 1 2.5 1 Z" fill="var(--orange)"/></svg>
          06 71 38 95 14
        </li>
        <li>
          <svg class="contact__icon" viewBox="0 0 12 12" aria-hidden="true"><rect x="0.5" y="2.5" width="11" height="7.5" fill="var(--orange)"/><path d="M0.8 2.8 L6 7 L11.2 2.8" fill="none" stroke="var(--card)" stroke-width="1"/></svg>
          bastiengolmier@quelmoto.fr
        </li>
        <li>
          <svg class="contact__icon" viewBox="0 0 12 12" aria-hidden="true"><g fill="none" stroke="var(--orange)" stroke-width="1"><circle cx="6" cy="6" r="5"/><ellipse cx="6" cy="6" rx="2.2" ry="5"/><path d="M1 6 H11 M2 3.5 H10 M2 8.5 H10"/></g></svg>
          www.bastiengolmier.fr
        </li>
      </ul>
    </div>
  </section>

  <section class="card card--back" aria-label="Verso">
    <div class="back-brand">
      <div class="brand-name">GOLMIER</div>
    </div>
    <p class="services">CONSULTING<span class="services__dot"></span>TRAINING<span class="services__dot"></span>DESIGN</p>
    <div class="social">
      <span class="social__rule"></span>
      <span class="social__dot"></span>
      <span>Carrivo</span>
      <span class="social__rule"></span>
    </div>
  </section>
</main>
</body>
</html>
```